Pressure Washing Hog Confinements

We clean and disinfect Hog confinements in-order to receive new pigs.

Needs to emphasis Clean Healthy barns (pigs), work done in timely manner, 100% satisfied, Bio-security rules followed. I do not have specific colors, no logo's.

Contact Information will be sent once design is agreed on.
Business Name - Brandt & Daughters Power Washing
Phone Number - Send latter
E-mail - Send latter
Web Address - Send latter

Target Market(s)

Farmers

Industry/Entity Type

Business

Requirements
Must have
• We are Insured
Bio-Security
100% Satisfied
Water Conservation

Size - 2 sided Postcard 8.5" x 5.5"
Nice to have
• I want to emphasize healthy and happy pigs because of a quality job done. Picture of pigs dose not need to be used but may be just an example.

Also attached is picture of a barn I would like to see used. on the back side. Every owner seeing this will know this is a hog barn and have an idea what we do.

```html
<!DOCTYPE html>
<html lang="en">
<head>
<meta charset="utf-8">
<title>Brandt &amp; Daughters Power Washing – Postcard</title>
<link href="https://fonts.googleapis.com/css2?family=Source+Sans+3:ital,wght@0,400;0,600;1,400;1,600&family=Arimo:wght@400&display=swap" rel="stylesheet">
<style>
  :root {
    --page-bg: #ece7df;
    --front-bg: #29231c;
    --brand-gray: #a39d94;
    --accent-blue: #2f8fd6;
    --back-top: #3a70bd;
    --back-mid: #5f95d4;
    --sky-low: #a9c6e8;
    --barn-roof: #b9bcbf;
    --barn-wall: #8e4a44;
    --grass: #6f8a4e;
    --gravel: #c4c0b8;
    --pig-pink: #efc3bd;
    --white: #ffffff;
    --ink: #222222;
    --rule: #9a9a9a;
  }
  * { box-sizing: border-box; margin: 0; padding: 0; }
  html, body { width: 896px; height: 1200px; overflow: hidden; }
  body {
    background: var(--page-bg);
    font-family: "Source Sans 3", sans-serif;
    position: relative;
  }
  .postcard {
    position: absolute;
    left: 69px;
    width: 774px;
    height: 498px;
    overflow: hidden;
    box-shadow: 0 3px 10px rgba(0,0,0,.25);
  }
  /* ---------- Front / mailing side ---------- */
  .postcard--front { top: 76px; background: var(--front-bg); }
  .front__photo {
    position: absolute;
    left: 50px; top: 60px;
    width: 360px; height: 250px;
    transform: rotate(-8deg);
    background: radial-gradient(ellipse at 55% 45%, #e9b9b1 0%, #c98f88 35%, #6b4a3c 75%, #3c2c22 100%);
    box-shadow: 0 2px 6px rgba(0,0,0,.5);
  }
  .mail-label {
    position: absolute; top: 27px; height: 66px;
    background: var(--white);
    font-family: "Arimo", sans-serif;
    color: var(--ink);
  }
  .mail-label--recipient { left: 520px; width: 135px; font-size: 12px; line-height: 14px; padding: 20px 0 0 14px; }
  .mail-label--indicia { left: 670px; width: 66px; font-size: 8.5px; line-height: 10px; text-align: center; padding-top: 8px; }
  .address-box {
    position: absolute; left: 372px; top: 245px;
    width: 358px; height: 144px;
    background: var(--white); border-radius: 8px;
  }
  .address-box__line {
    position: absolute; left: 48px; right: 48px; height: 1px; background: var(--rule);
  }
  .front__brand {
    position: absolute; left: 38px; top: 436px;
    font-size: 32px; color: var(--brand-gray);
  }
  .front__promises {
    position: absolute; right: 42px; top: 408px;
    text-align: right; font-style: italic;
    font-size: 27px; line-height: 36px; color: var(--accent-blue);
  }
  /* ---------- Back / info side ---------- */
  .postcard--back {
    top: 620px;
    background: linear-gradient(180deg, var(--back-top) 0%, var(--back-mid) 50%, var(--sky-low) 72%);
    color: var(--white);
  }
  .back__brand {
    position: absolute; left: 42px; top: 44px;
    font-size: 44px; font-weight: 600; font-style: italic;
    text-shadow: 0 2px 3px rgba(0,0,0,.35);
  }
  .back__contact { position: absolute; right: 38px; top: 34px; text-align: right; }
  .back__email { font-size: 15px; }
  .back__phone { margin-top: 8px; font-size: 17px; }
  .back__phone strong { font-size: 26px; font-weight: 600; }
  .back__web {
    position: absolute; left: 491px; top: 117px;
    width: 245px; height: 28px; border-radius: 5px;
    background: linear-gradient(180deg, #ffffff, #d4d4d4);
    color: var(--ink); font-size: 16px; letter-spacing: 1px;
    text-align: center; line-height: 28px;
  }
  .back__tagline {
    position: absolute; right: 36px; top: 210px;
    text-align: right; font-style: italic; font-size: 23px; line-height: 31px;
    text-shadow: 0 1px 2px rgba(0,0,0,.3);
  }
  .back__barn {
    position: absolute; left: 0; right: 0; top: 345px; height: 105px;
    background: linear-gradient(180deg, var(--barn-roof) 0%, var(--barn-roof) 40%, var(--barn-wall) 40%, var(--barn-wall) 70%, var(--grass) 70%, var(--grass) 100%);
  }
  .back__ground {
    position: absolute; left: 0; right: 0; top: 450px; bottom: 0;
    background: var(--gravel);
  }
  .back__pig {
    position: absolute; left: 57px; top: 223px;
    width: 200px; height: 250px; border-radius: 40px 40px 12px 12px;
    background: radial-gradient(ellipse at 50% 40%, #f6d6d1 0%, var(--pig-pink) 60%, #dca79f 100%);
  }
</style>
</head>
<body>

<section class="postcard postcard--front" aria-label="Postcard mailing side">
  <div class="front__photo" role="img" aria-label="Photo of a healthy young pig in a clean barn pen"></div>
  <div class="mail-label mail-label--recipient">Local<br>Postal Customer</div>
  <div class="mail-label mail-label--indicia">PRSRT STD<br>ECRWSS<br>U.S.POSTAGE<br><span style="font-size:10px">PAID</span><br>EDDM Retail</div>
  <div class="address-box">
    <span class="address-box__line" style="top:46px"></span>
    <span class="address-box__line" style="top:84px"></span>
    <span class="address-box__line" style="top:122px"></span>
  </div>
  <p class="front__brand">Brandt &amp; Daughters</p>
  <p class="front__promises">We are Insured Bio-Security<br>100% Satisfied Water Conservation</p>
</section>

<section class="postcard postcard--back" aria-label="Postcard information side">
  <div class="back__barn" role="img" aria-label="Photo of a long hog confinement barn with grain bins on a grass lot"></div>
  <div class="back__ground" role="img" aria-label="Gravel yard in front of the barn"></div>
  <div class="back__pig" role="img" aria-label="Photo of a clean, healthy pig standing in front of the barn"></div>
  <h1 class="back__brand">Brandt &amp; Daughters</h1>
  <div class="back__contact">
    <p class="back__email">info@brandtanddaughters.com</p>
    <p class="back__phone">Contact Us : <strong>5550147823</strong></p>
  </div>
  <p class="back__web">www.brandtanddaughters.com</p>
  <p class="back__tagline">We clean and disinfect Hog<br>confinements in-order to receive new pigs</p>
</section>

</body>
</html>
```